Business card for event manager / organizer "waiter service"

Draft of a new valuable business card for my company.
Events, personnel service providers, festivals

```html
<!DOCTYPE html>
<html lang="de">
<head>
<meta charset="utf-8">
<title>Lenno's Kellnerservice – Visitenkarte</title>
<link href="https://fonts.googleapis.com/css2?family=Lato:wght@400;700&display=swap" rel="stylesheet">
<style>
  :root {
    --stage: #3a3a3c;
    --card-dark: #231f22;
    --orange: #ee7a1a;
    --white: #ffffff;
    --text-light: #f1eeee;
    --violet: #5b2f7a;
    --violet-deep: #2a1634;
    --amber: #d8892b;
  }
  * { box-sizing: border-box; margin: 0; padding: 0; }
  html, body { width: 1200px; height: 689px; overflow: hidden; }
  body {
    background: var(--stage);
    font-family: "Lato", Arial, sans-serif;
    position: relative;
  }
  .card {
    position: absolute;
    top: 170px;
    width: 540px;
    height: 349px;
    border-radius: 18px;
    overflow: hidden;
  }
  /* front */
  .card-front { left: 40px; }
  .front-photo {
    position: absolute; inset: 0;
    background:
      radial-gradient(ellipse at 85% 0%, rgba(216,137,43,.85), transparent 55%),
      radial-gradient(ellipse at 30% 40%, rgba(150,90,190,.7), transparent 60%),
      linear-gradient(180deg, var(--violet) 0%, var(--violet-deep) 70%, #140b18 100%);
  }
  .front-brand {
    position: absolute; left: 34px; bottom: 48px;
    display: flex; align-items: center; gap: 14px;
  }
  .brand-square {
    width: 56px; height: 56px; background: var(--orange); border-radius: 4px;
  }
  .brand-name {
    font-weight: 700; font-size: 30px; color: var(--white); line-height: 1.05;
  }
  .brand-tagline {
    font-size: 13px; color: var(--white); margin-top: 6px; font-weight: 400;
  }
  /* back */
  .card-back { left: 620px; background: var(--card-dark); }
  .edge-strip {
    position: absolute; left: 0; top: 0; bottom: 0; width: 14px;
    background: linear-gradient(180deg, var(--white) 0 72%, var(--orange) 72% 100%);
  }
  .back-brand {
    position: absolute; right: 30px; top: 30px;
    display: flex; align-items: center; gap: 10px;
  }
  .back-brand .brand-square { width: 40px; height: 40px; }
  .back-brand .brand-name { font-size: 21px; }
  .back-brand .brand-tagline { font-size: 9.5px; margin-top: 3px; }
  .rule {
    position: absolute; height: 1px; background: var(--orange);
  }
  .rule-top { left: 250px; right: 30px; top: 96px; }
  .rule-mid { left: 40px; right: 240px; top: 240px; }
  .holder {
    position: absolute; left: 40px; top: 178px;
  }
  .holder-name { color: var(--orange); font-size: 28px; font-weight: 700; line-height: 1.1; }
  .holder-role { color: var(--text-light); font-size: 15px; margin-top: 2px; }
  .contact-list {
    position: absolute; left: 40px; top: 254px; list-style: none;
  }
  .contact-list li {
    display: flex; align-items: center; gap: 9px;
    color: var(--text-light); font-size: 13px; line-height: 22px;
  }
  .contact-list svg { width: 12px; height: 12px; flex: none; }
  .address {
    position: absolute; right: 30px; top: 112px; text-align: right;
    color: var(--text-light); font-size: 13px; line-height: 20px;
  }
  .address .web { color: var(--orange); }
</style>
</head>
<body>

<section class="card card-front">
  <div class="front-photo" role="img" aria-label="Foto: Kellner mit Sektgläsern auf einem Tablett vor einer feiernden Menge im violetten und orangen Bühnenlicht"></div>
  <div class="front-brand">
    <div class="brand-square"></div>
    <div>
      <div class="brand-name">Lenno's<br>Kellnerservice</div>
      <div class="brand-tagline">Service mit Herz für jeden Anlass</div>
    </div>
  </div>
</section>

<section class="card card-back">
  <div class="edge-strip"></div>

  <div class="back-brand">
    <div class="brand-square"></div>
    <div>
      <div class="brand-name">Lenno's Kellnerservice</div>
      <div class="brand-tagline">Service mit Herz für jeden Anlass</div>
    </div>
  </div>
  <div class="rule rule-top"></div>

  <div class="address">
    Lenno's Kellner Service<br>
    Birkenweg 12, 45657 Musterstadt<br>
    <span class="web">lennos-kellnerservice.de</span>
  </div>

  <div class="holder">
    <div class="holder-name">Lenno Dachsberg</div>
    <div class="holder-role">Inhaber</div>
  </div>
  <div class="rule rule-mid"></div>

  <ul class="contact-list">
    <li>
      <svg viewBox="0 0 12 12" aria-hidden="true"><path d="M2.5 1l2 2.2-1 1.3a6 6 0 0 0 4 4l1.3-1 2.2 2-1.2 1.5C5.5 11 1 6.5 1 2.2z" fill="#ee7a1a"/></svg>
      02361 550 12 34 / 0170 555 01 23
    </li>
    <li>
      <svg viewBox="0 0 12 12" aria-hidden="true"><path d="M11 1L1 5.5l4 1.5 1.5 4z" fill="#ee7a1a"/></svg>
      info@lennos-kellnerservice.de
    </li>
    <li>
      <svg viewBox="0 0 12 12" aria-hidden="true"><circle cx="6" cy="6" r="5.5" fill="#ee7a1a"/></svg>
      /lennoskellnerservice
    </li>
  </ul>
</section>

</body>
</html>
```